We need a business card design, letterhead design and envelope design for our corporate image

We are looking for a corporate business card design, letterhead and envelope design to match the business card design. Logo is done.

```html
<!DOCTYPE html>
<html lang="en">
<head>
<meta charset="utf-8">
<title>Veronta Envelope Design</title>
<link href="https://fonts.googleapis.com/css2?family=Open+Sans:wght@400;600;700&display=swap" rel="stylesheet">
<style>
  :root {
    --backdrop: #dfdedf;
    --paper: #ffffff;
    --brand-yellow: #fcc812;
    --brand-grey: #5f5f61;
    --ink: #4a4a4c;
    --flap: #000000;
    --flap-text: #ffffff;
  }
  html, body {
    margin: 0;
    padding: 0;
    width: 1200px;
    height: 1135px;
    overflow: hidden;
    background: var(--backdrop);
    font-family: "Open Sans", Arial, sans-serif;
  }
  .canvas {
    position: relative;
    width: 1200px;
    height: 1135px;
  }
  .envelope {
    position: absolute;
    left: 141px;
    width: 918px;
    background: var(--paper);
    box-shadow: 0 12px 22px rgba(0, 0, 0, 0.22);
  }
  .envelope--front {
    top: 128px;
    height: 401px;
  }
  .envelope__band {
    position: absolute;
    left: 0;
    right: 0;
    bottom: 0;
    height: 8px;
    background: var(--brand-yellow);
  }
  .sender {
    position: absolute;
    left: 25px;
    top: 23px;
    display: flex;
    align-items: center;
    height: 70px;
  }
  .brand {
    display: flex;
    align-items: center;
    gap: 10px;
  }
  .brand__square {
    width: 22px;
    height: 22px;
    background: var(--brand-yellow);
  }
  .brand__name {
    font-size: 30px;
    font-weight: 600;
    color: var(--brand-grey);
    letter-spacing: -0.5px;
  }
  .sender__divider {
    width: 1px;
    height: 31px;
    background: var(--ink);
    margin: 0 11px 0 15px;
  }
  .sender__address {
    font-size: 13.6px;
    line-height: 18.5px;
    color: var(--ink);
  }
  .envelope--back {
    top: 604px;
    height: 403px;
  }
  .flap {
    position: absolute;
    left: 0;
    top: 0;
    width: 918px;
    height: 140px;
    display: block;
    overflow: visible;
  }
  .flap__shape {
    fill: var(--flap);
  }
  .flap__title {
    position: absolute;
    left: 0;
    right: 0;
    top: 57px;
    text-align: center;
    color: var(--flap-text);
    font-size: 24px;
    font-weight: 600;
    letter-spacing: 2.4px;
  }
  .flap__title sup {
    font-size: 13px;
    letter-spacing: 0;
    font-weight: 600;
    vertical-align: 9px;
  }
</style>
</head>
<body>
<main class="canvas">
  <section class="envelope envelope--front" aria-label="Envelope front">
    <div class="sender">
      <div class="brand">
        <span class="brand__square"></span>
        <span class="brand__name">Veronta</span>
      </div>
      <span class="sender__divider"></span>
      <address class="sender__address" style="font-style:normal">
        212 Meadow Ridge Rd.<br>
        Eastbrook CT. 06118
      </address>
    </div>
    <div class="envelope__band"></div>
  </section>

  <section class="envelope envelope--back" aria-label="Envelope back">
    <svg class="flap" viewBox="0 0 918 140" aria-hidden="true">
      <path class="flap__shape" d="M0 0 L918 0 L902 92 C895 120 868 139 835 139 L83 139 C50 139 23 120 16 92 Z"/>
    </svg>
    <div class="flap__title">SHIELD FINISH<sup>TM</sup></div>
  </section>
</main>
</body>
</html>
```